Powepoint Templates From Logo

We need 3 Powerpoint templates for use in a variety of presentations we develop and customize. Primary uses of the powerpoint presentations are for printed "pitch books" describing our firm's capabilities and approach (a lot of words with some design elements that we have developed), printed presentations of the results of financial evaluations of our clients (lots of charts and graphs) and as the talking points for speeches.

The design needs to be professional and "solid" to establish that we are capable of selling your multi-million dollar business, but also be a little different to show that we are not just boring MBA's.

Our current website and other materials have been developed internally and leave a great deal to be desired. I have initiated this project to demonstrate how much our look can be improved and, if successful, I hope to do much bigger projects in the future.
Updates

This is my first project and I thaank you all for your participation. Since I am new to this, I don;t know if I am providing the help and feedback as I should. Please feel free to let me know how I can be a better customer.

Target Market(s)

professionals (lawyers, accountaants), business owners, business groups, technology people

Industry/Entity Type

Financial

Requirements
Must have
• our logo
a place where logo of client can be inserted if appropriate
templates for the following pages
title page
standard bullet narrative page
page for charts and graphs to mostly fill the page
Should not have a lot of dark solid color that has to be printed.

Nice to have
• something to perk up the color a little

```html
<!DOCTYPE html>
<html lang="en">
<head>
<meta charset="utf-8">
<title>Project Title Here</title>
<link href="https://fonts.googleapis.com/css2?family=Oswald:wght@700&family=Arimo:wght@400;700&display=swap" rel="stylesheet">
<style>
  :root {
    --navy: #0b2a5f;
    --navy-text: #0d2f66;
    --edge-blue: #b9d3f3;
    --title-light: #dbe9fb;
    --title-mid: #9fc2ec;
    --footer-band: #e8f1fc;
    --white: #ffffff;
    --portrait-top: #7a8794;
    --portrait-bottom: #2a2f3a;
  }
  * { margin: 0; padding: 0; box-sizing: border-box; }
  html, body {
    width: 1200px;
    height: 900px;
    overflow: hidden;
    background: var(--white);
  }
  .slide {
    position: relative;
    width: 1200px;
    height: 900px;
    overflow: hidden;
    background: var(--white);
    font-family: "Arimo", Arial, sans-serif;
  }
  .slide__backdrop {
    position: absolute;
    inset: 0;
    width: 1200px;
    height: 900px;
  }
  .slide__portrait {
    position: absolute;
    left: 167px;
    top: 86px;
    width: 184px;
    height: 236px;
    border-radius: 22px;
    border: 2px solid var(--white);
    background: linear-gradient(180deg, var(--portrait-top) 0%, var(--portrait-bottom) 100%);
  }
  .slide__title {
    position: absolute;
    right: 40px;
    top: 62px;
    font-family: "Oswald", Impact, sans-serif;
    font-weight: 700;
    font-size: 60px;
    line-height: 1;
    letter-spacing: 0.5px;
    text-transform: uppercase;
    background: linear-gradient(180deg, var(--title-light) 0%, var(--title-light) 45%, var(--title-mid) 100%);
    -webkit-background-clip: text;
    background-clip: text;
    color: transparent;
  }
  .slide__subtitle {
    position: absolute;
    right: 40px;
    top: 428px;
    font-weight: 700;
    font-size: 42px;
    line-height: 1;
    color: var(--navy-text);
  }
  .brand {
    position: absolute;
    left: 62px;
    top: 742px;
  }
  .brand__name {
    font-weight: 700;
    font-size: 48px;
    line-height: 1;
    letter-spacing: 1px;
    color: var(--navy-text);
  }
</style>
</head>
<body>
  <main class="slide">
    <svg class="slide__backdrop" viewBox="0 0 1200 900" aria-hidden="true">
      <polygon points="0,0 1200,0 1200,246 0,600" fill="var(--navy)"/>
      <polygon points="0,600 1200,246 1200,258 0,612" fill="var(--edge-blue)"/>
      <rect x="0" y="877" width="1200" height="23" fill="var(--footer-band)"/>
    </svg>

    <div class="slide__portrait" role="img" aria-label="Portrait photo of the presenter"></div>

    <h1 class="slide__title">Project Title Here</h1>
    <p class="slide__subtitle">Sub title here</p>

    <div class="brand">
      <span class="brand__name">CALDERWOOD PARTNERS</span>
    </div>
  </main>
</body>
</html>
```